Verlindo Magician

I want the business card for my business to give to people who watch that later I will be employed to show magic here is my website http://www.verlindoillusions.example/I want the interesting design , i am very opened for formal and informal, I watch a lot of design so don't stick to the common shape and form but i hope it can also be produced the thing to write on will be the same as in picture that i will upload , i also will upload the logo for you that so can be easy to useDenis CostilleMagicianMAGICIAN BALSAMO 17 rue des Tilleuls - 25000 BESANÇON contact@verlindoillusions.example tel. 0381 946 157 tel. 0674 219 503

```html
<!DOCTYPE html>
<html lang="fr">
<head>
<meta charset="utf-8">
<title>Verlindo Magician – Business Card</title>
<link rel="stylesheet" href="https://fonts.googleapis.com/css2?family=Jost:wght@400;500&display=swap">
<style>
  :root {
    --page-bg: #e4e4e2;
    --card-white: #ffffff;
    --ink-black: #000000;
    --brand-red: #ea2227;
    --text-grey: #555555;
    --text-white: #ffffff;
    --figure-dark: #111111;
  }
  * { box-sizing: border-box; margin: 0; padding: 0; }
  html, body {
    width: 1125px; height: 1200px; overflow: hidden;
    background: var(--page-bg);
    font-family: "Jost", "Futura", sans-serif;
  }
  .canvas { position: relative; width: 1125px; height: 1200px; }

  .card {
    position: absolute; left: 170px; width: 826px; height: 470px;
    box-shadow: 0 2px 6px rgba(0,0,0,0.25);
    overflow: hidden;
  }
  .card--front { top: 106px; background: var(--card-white); }
  .card--back  { top: 638px; background: var(--brand-red); }

  .front-wave { position: absolute; left: 0; top: 0; width: 826px; height: 470px; }

  .holder {
    position: absolute; right: 50px; top: 30px; text-align: right;
  }
  .holder__name { color: var(--brand-red); font-size: 31px; font-weight: 400; line-height: 1.1; }
  .holder__role { color: var(--text-white); font-size: 21px; font-weight: 400; line-height: 1.2; }

  .contact {
    position: absolute; left: 49px; top: 252px; color: var(--text-grey);
    font-size: 20px; line-height: 26px;
  }
  .contact__address { margin-bottom: 22px; }
  .contact__list { list-style: none; }
  .contact__item { display: flex; align-items: center; gap: 10px; height: 26px; }
  .contact__icon { width: 18px; height: 18px; flex: none; }

  .brand-mark { position: absolute; left: 624px; top: 198px; width: 150px; text-align: center; }
  .brand-mark__figure {
    display: block; margin: 0 auto; width: 150px; height: 180px;
    background: linear-gradient(180deg, var(--figure-dark), #2a2a2a);
    border-radius: 60px 60px 12px 12px;
  }
  .brand-mark__name { margin-top: 6px; font-size: 28px; font-weight: 400; color: var(--ink-black); letter-spacing: 1px; }

  .back-figure {
    position: absolute; left: 317px; top: 80px; width: 228px; height: 290px;
    background: linear-gradient(180deg, var(--figure-dark), #262626);
    border-radius: 90px 90px 16px 16px;
  }
  .back-url {
    position: absolute; left: 0; right: 0; top: 398px; text-align: center;
    color: var(--text-white); font-size: 18px; letter-spacing: 2.4px;
  }
</style>
</head>
<body>
<main class="canvas">

  <section class="card card--front">
    <svg class="front-wave" viewBox="0 0 826 470" aria-hidden="true">
      <path fill="var(--ink-black)" d="M0,0 H826 V112 C700,124 575,95 440,58 C310,24 190,22 115,62 C60,92 20,145 0,198 Z"/>
      <path fill="none" stroke="var(--card-white)" stroke-width="4" d="M55,70 C170,20 330,22 470,72"/>
      <path fill="var(--brand-red)" d="M150,30 C300,18 430,62 575,98 C680,122 760,124 826,116 V146 C740,164 635,152 535,120 C410,80 290,34 150,30 Z"/>
    </svg>

    <div class="holder">
      <p class="holder__name">Marc Ravoulet</p>
      <p class="holder__role">Magician</p>
    </div>

    <div class="contact">
      <p>MAGICIAN VERLINDO</p>
      <p class="contact__address">17 rue des Tilleuls - 25000 BESANÇON</p>
      <ul class="contact__list">
        <li class="contact__item">
          <svg class="contact__icon" viewBox="0 0 24 24" aria-hidden="true"><path fill="var(--brand-red)" d="M6.6 10.8a15 15 0 0 0 6.6 6.6l2.2-2.2a1 1 0 0 1 1-.25 11.4 11.4 0 0 0 3.6.57 1 1 0 0 1 1 1V20a1 1 0 0 1-1 1A17 17 0 0 1 3 4a1 1 0 0 1 1-1h3.5a1 1 0 0 1 1 1c0 1.25.2 2.45.57 3.57a1 1 0 0 1-.25 1z"/></svg>
          <span>0381 946 157</span>
        </li>
        <li class="contact__item">
          <svg class="contact__icon" viewBox="0 0 24 24" aria-hidden="true"><path fill="var(--brand-red)" d="M6.6 10.8a15 15 0 0 0 6.6 6.6l2.2-2.2a1 1 0 0 1 1-.25 11.4 11.4 0 0 0 3.6.57 1 1 0 0 1 1 1V20a1 1 0 0 1-1 1A17 17 0 0 1 3 4a1 1 0 0 1 1-1h3.5a1 1 0 0 1 1 1c0 1.25.2 2.45.57 3.57a1 1 0 0 1-.25 1z"/></svg>
          <span>0674 219 503</span>
        </li>
        <li class="contact__item">
          <svg class="contact__icon" viewBox="0 0 24 24" aria-hidden="true"><rect x="3" y="6" width="18" height="12" fill="var(--brand-red)"/><path d="M3 6 L12 13 L21 6" fill="none" stroke="#fff" stroke-width="1.6"/></svg>
          <span>contact@verlindoillusions.example</span>
        </li>
        <li class="contact__item">
          <svg class="contact__icon" viewBox="0 0 24 24" aria-hidden="true"><circle cx="12" cy="12" r="10" fill="var(--brand-red)"/><path d="M8 7c2 1 3 3 2 5s1 4 3 5M14 5c0 2 2 3 4 3" fill="none" stroke="#fff" stroke-width="1.6"/></svg>
          <span>www.verlindoillusions.example</span>
        </li>
      </ul>
    </div>

    <div class="brand-mark">
      <span class="brand-mark__figure" role="img" aria-label="Black silhouette illustration of the magician in a jacket holding a playing card"></span>
      <p class="brand-mark__name">VERLINDO</p>
    </div>
  </section>

  <section class="card card--back">
    <div class="back-figure" role="img" aria-label="Large black silhouette illustration of the magician in a jacket holding a playing card"></div>
    <p class="back-url">www.verlindoillusions.example</p>
  </section>

</main>
</body>
</html>
```